Harbor Crestline (Business Card Design)

Need business cards designed. Something modern, chic, and sleek. Mabye the back of the card should be the navy blue that is in the logo and then just the logo on the back.

Target Market(s)

Those in the hotel, office, and renovation industry

Contact Information for Business Card

1. Logo 2. Dorian Fenwick 3. CEO/Founder 4. Phone: (833) HarbCre / (833) 427-2731 5. Email: dorian@theharborcrestline.com 6. Website: www.theharborcrestline.com

Font styles to use
Other font styles liked:
• Look at the logo font and base the font for everything else off of that.

Colors
0054AA
0677BA
7BADD7
CADEEF
E8F1F8

Requirements
Must have
• Colors that are associated in the logo
Nice to have
• Sleek modern clean and chic design.

```html
<!DOCTYPE html>
<html lang="en">
<head>
<meta charset="UTF-8">
<title>Harbor Crestline – Business Card</title>
<link href="https://fonts.googleapis.com/css2?family=Montserrat:wght@400;500;600;700&display=swap" rel="stylesheet">
<style>
  :root {
    --stage: #1c1d21;
    --navy: #0d1a45;
    --navy-deep: #0a1236;
    --navy-light: #1b2a6b;
    --gold: #d4a63f;
    --white: #ffffff;
  }
  * { box-sizing: border-box; margin: 0; padding: 0; }
  html, body { width: 1200px; height: 780px; overflow: hidden; }
  body {
    background: var(--stage);
    font-family: "Montserrat", sans-serif;
    color: var(--white);
    display: flex;
    align-items: center;
    justify-content: center;
    gap: 40px;
  }
  .card {
    position: relative;
    width: 540px;
    height: 310px;
    border-radius: 24px;
    border: 3px solid var(--gold);
    background: var(--navy);
    overflow: hidden;
  }

  /* Back of card */
  .card-back__pattern {
    position: absolute;
    inset: 0;
    background: linear-gradient(160deg, var(--navy-light) 0%, var(--navy) 45%, var(--navy-deep) 100%);
  }
  .card-back__brand {
    position: absolute;
    top: 36px;
    right: 38px;
    display: flex;
    align-items: center;
    gap: 8px;
    font-weight: 600;
    font-size: 13px;
    letter-spacing: 1.5px;
    text-transform: uppercase;
  }
  .brand-square {
    width: 12px;
    height: 12px;
    background: var(--white);
  }

  /* Front of card */
  .card-front__tab {
    position: absolute;
    top: 42px;
    right: 0;
    width: 40px;
    height: 34px;
    background: var(--gold);
  }
  .card-front__person {
    position: absolute;
    top: 36px;
    right: 58px;
    text-align: right;
  }
  .person-name {
    font-size: 30px;
    line-height: 1.1;
  }
  .person-name__first { color: var(--gold); font-weight: 700; }
  .person-name__last { color: var(--white); font-weight: 700; }
  .person-title {
    font-size: 15px;
    font-weight: 500;
    margin-top: 4px;
  }
  .card-front__brand {
    position: absolute;
    left: 38px;
    top: 128px;
    display: flex;
    align-items: center;
    gap: 10px;
    font-weight: 600;
    font-size: 20px;
    letter-spacing: 2px;
    text-transform: uppercase;
  }
  .card-front__brand .brand-square { width: 18px; height: 18px; }
  .card-front__address {
    position: absolute;
    left: 38px;
    top: 168px;
    font-size: 13px;
    line-height: 1.45;
  }
  .card-front__contacts {
    position: absolute;
    left: 38px;
    bottom: 26px;
    list-style: none;
    font-size: 12.5px;
    line-height: 1.55;
  }
  .contact-item {
    display: flex;
    align-items: center;
    gap: 9px;
  }
  .contact-item svg { width: 13px; height: 13px; flex: none; }
</style>
</head>
<body>

  <section class="card card-back" aria-label="Card back">
    <div class="card-back__pattern" role="img" aria-label="Repeating brand pattern in navy tones"></div>
    <div class="card-back__brand">
      <span class="brand-square"></span>
      <span>Harbor Crestline</span>
    </div>
  </section>

  <section class="card card-front" aria-label="Card front">
    <div class="card-front__tab"></div>
    <div class="card-front__person">
      <p class="person-name"><span class="person-name__first">Dorian</span> <span class="person-name__last">Fenwick</span></p>
      <p class="person-title">CEO/Founder</p>
    </div>

    <div class="card-front__brand">
      <span class="brand-square"></span>
      <span>Harbor Crestline</span>
    </div>

    <address class="card-front__address" style="font-style:normal">
      4120 Lindell Ave<br>
      Suite 2200, Marston, MD 21077
    </address>

    <ul class="card-front__contacts">
      <li class="contact-item">
        <svg viewBox="0 0 24 24" fill="var(--gold)" aria-hidden="true"><path d="M6.6 10.8a15.1 15.1 0 0 0 6.6 6.6l2.2-2.2a1 1 0 0 1 1-.25 11.4 11.4 0 0 0 3.6.57 1 1 0 0 1 1 1V20a1 1 0 0 1-1 1A17 17 0 0 1 3 4a1 1 0 0 1 1-1h3.5a1 1 0 0 1 1 1c0 1.25.2 2.45.57 3.6a1 1 0 0 1-.25 1z"/></svg>
        <span>(833) HarbCre / (833) 427-2731</span>
      </li>
      <li class="contact-item">
        <svg viewBox="0 0 24 24" fill="none" stroke="var(--gold)" stroke-width="2.2" aria-hidden="true"><circle cx="12" cy="12" r="9.5"/><path d="M2.5 12h19M12 2.5c3 3.2 3 15.8 0 19M12 2.5c-3 3.2-3 15.8 0 19"/></svg>
        <span>www.theharborcrestline.com</span>
      </li>
      <li class="contact-item">
        <svg viewBox="0 0 24 24" fill="none" stroke="var(--gold)" stroke-width="2.2" aria-hidden="true"><rect x="2.5" y="5" width="19" height="14" rx="1.5"/><path d="M3 6l9 7 9-7"/></svg>
        <span>dorian@theharborcrestline.com</span>
      </li>
    </ul>
  </section>

</body>
</html>
```